Marwick Law Letterhead

We need a new letterhead design for a Law Firm. The address for the law firm is 1475 Calloway Street, Suite 210, Houston, Texas 77041. Phone Number: 832-361-9027; Fax Number: 832-614-7359. The logo is uploaded to the project.

```html
<!DOCTYPE html>
<html lang="en">
<head>
<meta charset="utf-8">
<title>Marwick Law Letterhead</title>
<link href="https://fonts.googleapis.com/css2?family=Montserrat:wght@400;500;600&display=swap" rel="stylesheet">
<style>
  :root {
    --backdrop: #e8e8ea;
    --paper: #ffffff;
    --ink: #2a2a2a;
    --navy: #1a2f5c;
    --red: #d51c29;
    --red-deep: #6e0a12;
  }
  * { margin: 0; padding: 0; box-sizing: border-box; }
  html, body {
    width: 1200px; height: 960px; overflow: hidden;
    background: var(--backdrop);
    font-family: "Montserrat", Arial, sans-serif;
    color: var(--ink);
  }
  .letterhead {
    position: absolute; left: 275px; top: 20px;
    width: 650px; height: 920px;
    background: var(--paper);
    box-shadow: 0 6px 24px rgba(0,0,0,0.12);
    overflow: hidden;
  }
  .brand {
    position: absolute; left: 48px; top: 92px;
    display: flex; align-items: center; gap: 10px;
  }
  .brand-mark { width: 26px; height: 26px; background: var(--navy); }
  .brand-name {
    font-size: 26px; font-weight: 500; color: var(--navy);
    letter-spacing: 0.5px;
  }
  .contact {
    position: absolute; left: 440px; top: 40px;
    font-size: 11px; line-height: 1.35;
  }
  .contact-line { display: flex; align-items: center; gap: 7px; margin-top: 2px; }
  .contact-line svg { width: 10px; height: 10px; }
  .header-rule {
    position: absolute; left: 110px; right: 40px; top: 166px;
    height: 3px; background: var(--red);
  }
  .letter-body {
    position: absolute; left: 120px; right: 45px; top: 205px;
    font-size: 11px; line-height: 1.4;
  }
  .recipient { margin-bottom: 2px; }
  .letter-body p { margin-bottom: 16px; }
  .closing { margin-top: 6px; font-size: 12px; }
  .signature {
    display: block; width: 110px; height: 34px; margin-top: 6px;
    background: linear-gradient(90deg, #f1f1f1, #e2e2e2);
    border-radius: 3px;
  }
  .footer-bands { position: absolute; left: 0; bottom: 0; width: 650px; height: 120px; }
</style>
</head>
<body>
  <main class="letterhead">
    <div class="brand">
      <span class="brand-mark"></span>
      <span class="brand-name">Marwick Law</span>
    </div>

    <address class="contact">
      1475 Calloway Street,<br>
      Suite 210, Houston,<br>
      Texas 77041
      <div class="contact-line">
        <svg viewBox="0 0 10 10" aria-hidden="true"><path d="M2 1 L4 1 L4.8 3 L3.6 4 Q4.6 5.6 6 6.4 L7 5.2 L9 6 L9 8 Q8.6 9 7.6 9 Q1 8.4 1 2 Q1 1 2 1Z" fill="#d51c29"/></svg>
        832-361-9027
      </div>
      <div class="contact-line">
        <svg viewBox="0 0 10 10" aria-hidden="true"><rect x="1" y="3.5" width="8" height="5" rx="1" fill="#d51c29"/><rect x="2.5" y="1" width="5" height="3" fill="#d51c29"/><rect x="3" y="6" width="4" height="1" fill="#fff"/></svg>
        832-614-7359
      </div>
    </address>

    <div class="header-rule"></div>

    <section class="letter-body">
      <div class="recipient">Mr/s<br>First Name and Last Name<br>Company Name<br>Address</div>
      <p>Lorem ipsum dolor sit amet,consectetur adipiscing sed do eiusmod tempor incididunt laboreet dolore magna aliqua.Ut enim ad minim.veniam, quis nostrud exercitation ullamco laboris nisi ut aliquip exea commodo consequat.Lorem ipsum dolor sit amet,consectetur adipiscing sed do eiusmod tempor incididunt.labore et dolore magna aliqua. Ut enim</p>
      <p>Lorem ipsum dolor sit amet, consectetur adipiscing sed do eiusmod tempor incididunt labore et dolore magna aliqua. Ut enim ad minim veniam, quis nostrud exercitation ullamco laboris nisi ut aliquip exea commodo consequat.Duis aute irure dolor in reprehenderit in voluptate velit esse cillum irure dolor in reprehenderit in voluptate velit esse irure</p>
      <p>Lorem ipsum dolor sit amet, consectetur adipiscing sed do eiusmod tempor incididunt labore et dolore magna aliqua. consequat. Duis aute irure dolor in.reprehenderit in voluptate velit esse cillum dolore eu fugiat nulla pariatur. Excepteur sint occaecat cupidatat non proident, sunt in culpa qui officia deserunt mollit,</p>
      <p>Lorem ipsum dolor sit amet, consectetur adipiscing sed do eiusmod tempor incididunt labore et dolore magna aliqua. Ut enim Lorem ipsum dolor sit amet, consectetur adipiscing sed do eiusmod tempor incididunt labore et dolore magna aliqua. Ut enim Lorem ipsum aliqua.ipsum</p>
      <p>Lorem ipsum dolor sit amet, consectetur adipiscing sed do eiusmod tempor incididunt labore et dolore magna aliqua. Ut enim ad minim veniam, quis nostrud exercitation ullamco laboris nisi ut aliquip exea commodo consequat.Duis aute irure dolor in reprehenderit in voluptate velit esse cillum irure dolor in reprehenderit in voluptate velit esse irure</p>
      <p>Lorem ipsum dolor sit amet, consectetur adipiscing sed do eiusmod tempor incididunt labore et dolore magna aliqua. Ut enim ad minim veniam, quis nostrud exercitation ullamco laboris nisi ut aliquip exea commodo consequat.Duis aute irure dolor in reprehenderit in voluptate velit esse cillum irure dolor in reprehenderit in voluptate velit esse irure</p>
      <div class="closing">Regards</div>
      <span class="signature" role="img" aria-label="Handwritten signature of the sender"></span>
    </section>

    <svg class="footer-bands" viewBox="0 0 650 120" aria-hidden="true">
      <defs>
        <linearGradient id="redBand" x1="0" y1="0" x2="1" y2="0">
          <stop offset="0" stop-color="#d51c29"/>
          <stop offset="0.55" stop-color="#d51c29"/>
          <stop offset="1" stop-color="#6e0a12"/>
        </linearGradient>
      </defs>
      <polygon class="band-navy" points="0,86 352,86 362,120 0,120" fill="#1a2f5c"/>
      <polygon class="band-red" points="368,22 650,22 650,120 378,120 362,70" fill="url(#redBand)"/>
    </svg>
  </main>
</body>
</html>
```